Las Vegas transportation company needs a dynamic design for business cards

We are a transportation management company based in Las Vegas specializing in operating and maintaining public transit systems. We want to keep our existing logo but would like to design business cards that feature one or more transit systems (e.g. monorail, train, bus) and maybe also the Las Vegas landscape.

```html
<!DOCTYPE html>
<html lang="en">
<head>
<meta charset="utf-8">
<title>Mesa Line Group – Business Card</title>
<link rel="stylesheet" href="https://fonts.googleapis.com/css2?family=Cinzel:wght@600&family=Lato:wght@400&display=swap">
<style>
  :root {
    --navy: #0c1f66;
    --sky: #8ab6e6;
    --white: #ffffff;
    --page: #e9e9ec;
    --night: #2b2620;
    --photo: #8a9bb3;
  }
  * { margin: 0; padding: 0; box-sizing: border-box; }
  html, body { width: 1200px; height: 900px; overflow: hidden; }
  body { background: var(--page); position: relative; font-family: "Lato", sans-serif; }

  .card {
    position: absolute; left: 250px; width: 700px; height: 400px;
    overflow: hidden; box-shadow: 0 6px 18px rgba(0,0,0,.18);
  }
  .card--back { top: 40px; }
  .card--front { top: 460px; background: var(--white); }

  /* back side */
  .cityscape { position: absolute; inset: 0; background: var(--night); }
  .transit-photo {
    position: absolute; border-radius: 50%; border: 3px solid var(--white);
    background: var(--photo);
  }
  .transit-photo--bus { left: 240px; top: 0; width: 180px; height: 180px; }
  .transit-photo--train { left: 500px; top: 85px; width: 175px; height: 175px; }
  .transit-photo--monorail { left: 85px; top: 175px; width: 205px; height: 205px; }

  /* front side */
  .wave { position: absolute; inset: 0; }
  .holder { position: absolute; left: 48px; top: 50px; color: var(--navy); }
  .holder__name {
    font-family: "Cinzel", serif; font-weight: 600; font-size: 30px; letter-spacing: 1px; line-height: 1;
  }
  .holder__title { font-size: 17px; margin-top: 4px; color: #1a1a40; }

  .contact { position: absolute; left: 72px; top: 150px; color: #1a1a2e; font-size: 17px; }
  .contact__row { display: flex; align-items: center; gap: 10px; line-height: 26px; }
  .contact__icon { width: 20px; height: 20px; fill: var(--navy); }
  .contact__address { margin-top: 18px; padding-left: 30px; line-height: 24px; }

  .brand {
    position: absolute; left: 372px; top: 68px; display: flex; align-items: center; gap: 12px;
    white-space: nowrap;
  }
  .brand__dot { width: 20px; height: 20px; border-radius: 50%; background: var(--navy); flex: none; }
  .brand__name {
    font-family: "Cinzel", serif; font-weight: 600; font-size: 26px; color: var(--navy);
    letter-spacing: .5px; line-height: 1;
  }

  .website {
    position: absolute; right: 40px; bottom: 36px; color: var(--white); font-size: 17px; letter-spacing: .3px;
  }
</style>
</head>
<body>
  <section class="card card--back">
    <div class="cityscape" role="img" aria-label="Night view of the Las Vegas Strip with illuminated hotels and a lit fountain"></div>
    <div class="transit-photo transit-photo--bus" role="img" aria-label="Photo of a double-decker city bus"></div>
    <div class="transit-photo transit-photo--train" role="img" aria-label="Photo of a diesel locomotive on a rail track"></div>
    <div class="transit-photo transit-photo--monorail" role="img" aria-label="Photo of a monorail train on an elevated track"></div>
  </section>

  <section class="card card--front">
    <svg class="wave" viewBox="0 0 700 400" preserveAspectRatio="none" aria-hidden="true">
      <path fill="var(--sky)" d="M0,318 C190,326 320,292 455,214 C330,298 200,338 0,336 Z"/>
      <path fill="var(--navy)" d="M0,342 C200,348 330,306 460,230 C550,178 630,140 700,118 L700,400 L0,400 Z"/>
    </svg>

    <div class="holder">
      <h1 class="holder__name">Daniel Reyes</h1>
      <p class="holder__title">Managing Director</p>
    </div>

    <div class="contact">
      <p class="contact__row">
        <svg class="contact__icon" viewBox="0 0 24 24" aria-hidden="true"><path d="M6.6 10.8a15.1 15.1 0 0 0 6.6 6.6l2.2-2.2a1 1 0 0 1 1-.25 11.4 11.4 0 0 0 3.6.57 1 1 0 0 1 1 1V20a1 1 0 0 1-1 1A17 17 0 0 1 3 4a1 1 0 0 1 1-1h3.5a1 1 0 0 1 1 1c0 1.25.2 2.45.57 3.57a1 1 0 0 1-.25 1z"/></svg>
        <span>702-555 0148</span>
      </p>
      <p class="contact__row">
        <svg class="contact__icon" viewBox="0 0 24 24" aria-hidden="true"><path d="M2 5h20v14H2z M2 5l10 8 10-8" fill="none" stroke="var(--navy)" stroke-width="2"/></svg>
        <span>info@mesalinegroup.com</span>
      </p>
      <p class="contact__address">88 Fremont Loop<br>Las Vegas, 89101</p>
    </div>

    <div class="brand">
      <span class="brand__dot"></span>
      <span class="brand__name">Mesa Line Group</span>
    </div>

    <p class="website">www.mesalinegroup.com</p>
  </section>
</body>
</html>
```